CrestHornSupply.com

I need a new webdesign for a company in the San Jose/SF Bay area that showcases the financial benefits of buying used band instruments for junior high students.This would be opposed to the current and costly option of renting cheap quality instruments from the 2 or 3 local music stores that charge a monthly fee that over the years charges the buyer 3 or 4x over..
Instruments: focus in on Alto Sax, Trumpet, Flute, Clarinet, Trombone, Tenor Sax, Baritone
Target middle schools are Larkfield Middle School and Maple Middle School in San Jose, CA. Both have award winning band programs.
Files attached may or may not be important.
Tabs Needed and funtional
Contact
Shopping Cart
Select Instrument
Checkout
Add to Cart, etc.
Instuments
quantity, etc.
trade in your instrument/sell your instrument
ability to add or take away new instruments for sale. including pictures
Additional questions or info, feel free to ask
Updates
Hi Designers,
Project Deadline Extended
Reason: In the next week you will be receiving specific content that will be required to be had on the website.
New desigins are still welcome. Please continue to contact me if you have questions about your individual designs.
Thanks!
Crest Horn

```html
<!DOCTYPE html>
<html lang="en">
<head>
<meta charset="utf-8">
<title>Crest Horn – Blog</title>
<link rel="stylesheet" href="https://fonts.googleapis.com/css2?family=Lato:wght@300;400;700;900&family=Montserrat:wght@400;700&family=Open+Sans:wght@400;600&display=swap">
<style>
:root{
  --page:#ffffff;
  --backdrop:#efefef;
  --ink:#222222;
  --text:#444444;
  --muted:#777777;
  --rule:#e3e3e3;
  --accent:#3c8a6c;
  --photo-a:#c9a892;
  --photo-b:#6d5a52;
  --shop-a:#b86a7a;
  --shop-b:#6a8a5a;
}
*{box-sizing:border-box;margin:0;padding:0}
html,body{width:900px;height:1200px;overflow:hidden}
body{background:var(--page);font-family:"Open Sans",Arial,sans-serif;color:var(--text);position:relative}
.backdrop{position:absolute;left:0;top:0;width:900px;height:912px;background:var(--backdrop)}
.page{position:absolute;left:113px;top:0;width:674px;height:912px;background:var(--page);overflow:hidden}
.abs{position:absolute}
.topbar{font-size:6px;color:var(--ink);top:6px}
.brand{left:0;width:674px;top:12px;text-align:center;font-family:"Lato",sans-serif;font-weight:900;font-size:32px;color:var(--ink);letter-spacing:1px}
.nav{left:0;top:63px;width:674px;height:23px;border-top:1px solid var(--rule);border-bottom:3px solid var(--ink);font-family:"Montserrat",sans-serif}
.nav .search{position:absolute;left:0;top:0;width:134px;height:19px;border-right:1px solid var(--rule);font-family:"Open Sans",sans-serif;font-size:6px;color:var(--ink);padding:5px 0 0 12px;display:flex;gap:8px;align-items:center}
.nav .item{position:absolute;top:5px;font-size:8px;font-weight:700;color:var(--ink)}
.nav .item.dim{color:#555}
.nav .cart{position:absolute;left:539px;top:0;height:19px;border-left:1px solid var(--rule);padding:5px 0 0 12px;font-family:"Open Sans",sans-serif;font-size:6.5px;color:var(--ink);display:flex;gap:8px;align-items:center}
.crumb{left:10px;top:93px;font-size:5px;color:var(--ink)}
.page-title{left:10px;top:98px;font-family:"Lato",sans-serif;font-weight:300;font-size:18px;color:var(--ink)}
.title-rule{left:0;top:122px;width:505px;border-top:1px solid var(--rule)}
.post-title{left:10px;width:475px;font-family:"Lato",sans-serif;font-weight:700;font-size:14.5px;line-height:15px;color:#333;letter-spacing:.2px}
.post-title.feature{color:var(--accent)}
.photo{left:39px;width:427px;height:140px}
.copy{left:10px;width:486px;font-size:6.3px;line-height:7px;color:var(--text);letter-spacing:.3px}
.copy p{margin-bottom:6px}
.meta{left:10px;width:486px;height:14px;border-top:1px solid var(--rule);font-size:5.5px;color:var(--muted);display:flex;align-items:center;gap:18px;padding-top:4px}
.meta b{color:var(--ink)}
.meta span{display:flex;align-items:center;gap:3px}
.btn{margin-left:auto;font-size:5.5px;font-weight:600;border:1px solid #ccc;border-radius:6px;padding:1px 8px;color:var(--ink);background:#fff}
.btn.on{background:var(--accent);border-color:var(--accent);color:#fff}
.sidebar{left:506px;top:86px;width:168px;height:826px;border-left:1px solid var(--rule)}
.side-head{position:absolute;left:10px;font-family:"Montserrat",sans-serif;font-weight:700;font-size:7.5px;color:var(--ink)}
.side-rule{position:absolute;left:0;width:168px;border-top:1px solid var(--rule)}
.recent{position:absolute;left:10px;width:148px;font-size:5.3px;line-height:6px;color:var(--text)}
.recent h4{font-size:6px;font-weight:600;color:var(--ink);margin-bottom:5px;line-height:6.5px}
.recent .by{display:flex;gap:16px;margin-top:8px;color:var(--ink)}
.recent .by span{display:flex;align-items:center;gap:4px}
.tags{position:absolute;left:10px;top:202px;font-size:6px;line-height:12px;color:var(--ink)}
.tags .sel{color:var(--accent)}
</style>
</head>
<body>
<div class="backdrop"></div>

<div class="page">
  <div class="abs topbar" style="left:10px">Login</div>
  <div class="abs topbar" style="left:44px">Register</div>
  <div class="abs topbar" style="left:631px">$ - USD ▾</div>
  <div class="abs brand">Crest Horn</div>

  <nav class="abs nav">
    <div class="search">
      <svg width="9" height="9" viewBox="0 0 10 10"><circle cx="6" cy="4" r="3" fill="none" stroke="#222" stroke-width="1"/><line x1="4" y1="6" x2="1" y2="9" stroke="#222"/></svg>Search
    </div>
    <span class="item" style="left:175px">HOME</span>
    <span class="item dim" style="left:244px">SHOP ▾</span>
    <span class="item" style="left:310px">SALE ▾</span>
    <span class="item" style="left:373px">BLOG</span>
    <span class="item" style="left:438px">CONTACT US</span>
    <div class="cart">
      <svg width="12" height="9" viewBox="0 0 12 9"><path d="M0 1h2l2 5h6l1-4H3" fill="none" stroke="#222" stroke-width="0.9"/><circle cx="5" cy="8" r="0.8" fill="#222"/><circle cx="9" cy="8" r="0.8" fill="#222"/></svg>3 ITEMS - $150.00
    </div>
  </nav>

  <div class="abs crumb">HOME » BLOG</div>
  <h1 class="abs page-title">Blog</h1>
  <div class="abs title-rule"></div>

  <h2 class="abs post-title feature" style="top:136px">Why buying a used alto sax beats years of monthly rental fees for your band student</h2>
  <div class="abs photo" style="top:174px;background:linear-gradient(100deg,var(--photo-b),var(--photo-a) 45%,#e7d8cc)" role="img" aria-label="Photo of a student with a used alto saxophone"></div>
  <div class="abs copy" style="top:324px">
    <p>Lorem ipsum dolor sit amet, consectetur adipiscing elit. Nullam odio nunc, varius sit amet tristique at, tincidunt ac ante. Phasellus tristique turpis in elit convallis vel convallis ante consequat. Donec eu dolor erat. Morbi pretium orci sed nibh porttitor vitae posuere neque pulvinar. Donec malesuada augue nisi. Suspendisse quis justo orci. Etiam sem justo, accumsan in fermentum eget, tincidunt iaculis sapien.</p>
    <p>Sed congue sapien convallis ante consequat ultrices. Pellentesque habitant morbi tristique senectus et netus et malesuada fames ac turpis egestas. Maecenas aliquam ultrices sapien, ut cursus elit fringilla et. Sed eu tincidunt erat. Nam enim sapien, luctus et eleifend nec, fringilla non nisl. Cum sociis natoque penatibus et magnis dis parturient montes, nascetur ridiculus mus. Pellentesque tristique arcu at mi pellentesque vel lobortis est congue. Mauris et nisl sed quam luctus pellentesque sit amet sit amet justo. Praesent vitae augue erat, vitae volutpat velit. Cras justo sem, condimentum ut condimentum at, laoreet vel turpis.</p>
    <p>Morbi at nulla at erat aliquet dapibus. In pretium porttitor nunc quis sodales. Morbi ut leo vitae turpis egestas faucibus at id justo. In quis augue ligula, sed hendrerit sapien. Curabitur consectetur leo ac magna placerat quis vulputate felis adipiscing. Fusce iaculis sodales laoreet. Mauris ac suscipit quam. Curabitur nec metus in elit posuere posuere.</p>
  </div>
  <div class="abs meta" style="top:433px">
    <span>May 22, 2012</span>
    <span><svg width="8" height="8" viewBox="0 0 8 8"><circle cx="4" cy="2.5" r="2" fill="none" stroke="#555" stroke-width=".7"/><path d="M0.5 8c0-2 1.5-3 3.5-3s3.5 1 3.5 3" fill="none" stroke="#555" stroke-width=".7"/></svg>written by <b>Admin</b></span>
    <span><svg width="9" height="7" viewBox="0 0 9 7"><ellipse cx="4.5" cy="3" rx="4" ry="2.5" fill="none" stroke="#555" stroke-width=".7"/></svg>20 comments</span>
    <span class="btn on">Post Comment</span>
  </div>

  <h2 class="abs post-title" style="top:478px">Quality used trumpets and flutes, ready for band</h2>
  <div class="abs photo" style="top:502px;background:linear-gradient(90deg,var(--shop-b),var(--shop-a) 40%,#9a7a8a 70%,#c9b8c0)" role="img" aria-label="Photo of families shopping for used instruments"></div>
  <div class="abs copy" style="top:656px">
    <p>Lorem ipsum dolor sit amet, consectetur adipiscing elit. Nullam odio nunc, varius sit amet tristique at, tincidunt ac ante. Phasellus tristique turpis in elit convallis vel convallis ante consequat. Donec eu dolor erat. Morbi pretium orci sed nibh porttitor vitae posuere neque pulvinar. Donec malesuada augue nisi. Suspendisse quis justo orci. Etiam sem justo, accumsan in fermentum eget, tincidunt iaculis sapien.</p>
    <p>Sed congue sapien convallis ante consequat ultrices. Pellentesque habitant morbi tristique senectus et netus et malesuada fames ac turpis egestas. Maecenas aliquam ultrices sapien, ut cursus elit fringilla et. Sed eu tincidunt erat. Nam enim sapien, luctus et eleifend nec, fringilla non nisl. Cum sociis natoque penatibus et magnis dis parturient montes, nascetur ridiculus mus. Pellentesque tristique arcu at mi pellentesque vel lobortis est congue. Mauris et nisl sed quam luctus pellentesque sit amet sit amet justo. Praesent vitae augue erat, vitae volutpat velit. Cras justo sem, condimentum ut condimentum at, laoreet vel turpis.</p>
    <p>Morbi at nulla at erat aliquet dapibus. In pretium porttitor nunc quis sodales. Morbi ut leo vitae turpis egestas faucibus at id justo. In quis augue ligula, sed hendrerit sapien. Curabitur consectetur leo ac magna placerat quis vulputate felis adipiscing. Fusce iaculis sodales laoreet. Mauris ac suscipit quam. Curabitur nec metus in elit posuere posuere.</p>
  </div>
  <div class="abs meta" style="top:762px">
    <span>May 22, 2012</span>
    <span><svg width="8" height="8" viewBox="0 0 8 8"><circle cx="4" cy="2.5" r="2" fill="none" stroke="#555" stroke-width=".7"/><path d="M0.5 8c0-2 1.5-3 3.5-3s3.5 1 3.5 3" fill="none" stroke="#555" stroke-width=".7"/></svg>written by <b>Admin</b></span>
    <span><svg width="9" height="7" viewBox="0 0 9 7"><ellipse cx="4.5" cy="3" rx="4" ry="2.5" fill="none" stroke="#555" stroke-width=".7"/></svg>20 comments</span>
    <span class="btn">Post Comment</span>
  </div>

  <h2 class="abs post-title" style="top:810px">Trade in or sell the clarinet, trombone or baritone your student has outgrown</h2>
  <div class="abs copy" style="top:847px">
    <p>Sed congue sapien convallis ante consequat ultrices. Pellentesque habitant morbi tristique senectus et netus et malesuada fames ac turpis egestas. Maecenas aliquam ultrices sapien, ut cursus elit fringilla et. Sed eu tincidunt erat. Nam enim sapien, luctus et eleifend nec, fringilla non nisl. Cum sociis natoque penatibus et magnis dis parturient montes, nascetur ridiculus mus. Praesent vitae augue erat, vitae volutpat velit.</p>
  </div>
  <div class="abs meta" style="top:890px">
    <span>May 22, 2012</span>
    <span><svg width="8" height="8" viewBox="0 0 8 8"><circle cx="4" cy="2.5" r="2" fill="none" stroke="#555" stroke-width=".7"/><path d="M0.5 8c0-2 1.5-3 3.5-3s3.5 1 3.5 3" fill="none" stroke="#555" stroke-width=".7"/></svg>written by <b>Admin</b></span>
    <span><svg width="9" height="7" viewBox="0 0 9 7"><ellipse cx="4.5" cy="3" rx="4" ry="2.5" fill="none" stroke="#555" stroke-width=".7"/></svg>20 comments</span>
    <span class="btn">Post Comment</span>
  </div>

  <aside class="abs sidebar">
    <div class="side-head" style="top:6px">RECENT ARTICLES</div>
    <div class="side-rule" style="top:21px"></div>
    <div class="recent" style="top:28px">
      <h4>Renting vs. buying: what band families really pay</h4>
      Ut enim ad minima veniam, quis nostrum exerci suscipit laboriosam, nisi ut aliquid ex ea commo autem vel eum iure reprehenderit qui in ea
      <div class="by"><span><svg width="8" height="8" viewBox="0 0 8 8"><circle cx="4" cy="2.5" r="2" fill="none" stroke="#555" stroke-width=".7"/><path d="M0.5 8c0-2 1.5-3 3.5-3s3.5 1 3.5 3" fill="none" stroke="#555" stroke-width=".7"/></svg>Admin</span><span><svg width="9" height="7" viewBox="0 0 9 7"><ellipse cx="4.5" cy="3" rx="4" ry="2.5" fill="none" stroke="#555" stroke-width=".7"/></svg>20 comments</span></div>
    </div>
    <div class="side-rule" style="top:92px;left:10px;width:148px"></div>
    <div class="recent" style="top:101px">
      <h4>Tenor sax care tips for new players</h4>
      Ut enim ad minima veniam, quis nostrum exerci suscipit laboriosam, nisi ut aliquid ex ea commo autem vel eum iure reprehenderit qui in ea
      <div class="by"><span><svg width="8" height="8" viewBox="0 0 8 8"><circle cx="4" cy="2.5" r="2" fill="none" stroke="#555" stroke-width=".7"/><path d="M0.5 8c0-2 1.5-3 3.5-3s3.5 1 3.5 3" fill="none" stroke="#555" stroke-width=".7"/></svg>Admin</span><span><svg width="9" height="7" viewBox="0 0 9 7"><ellipse cx="4.5" cy="3" rx="4" ry="2.5" fill="none" stroke="#555" stroke-width=".7"/></svg>20 comments</span></div>
    </div>
    <div class="side-rule" style="top:174px"></div>
    <div class="side-head" style="top:181px">TAGS</div>
    <div class="side-rule" style="top:195px"></div>
    <div class="tags">All<br><span class="sel">Blog Tags</span><br>Sample</div>
  </aside>
</div>
</body>
</html>
```